Brintel Works - Fast, Efficient and Gas Mainteance for Domestic, Commercial and Industrial clients

We are in the process of purchasing a new business and would like to get a new logo and business card.
Business is a gas maintenance business that also does new gas installations.
Has been established since 1988.
Services include:
Install all types of gas appliances & equipment inc. hot water units
Maintain / repair / replace all types of gas appliances & equipment

Target Market(s)

Domestic, Commercial and Industrial clients

Industry/Entity Type

Business

Contact Information for Business Card

admin@brintelworks.com.au
07 3918 4726
Brintel Works PTY LTD

Logo Text

Gas Fitting & Plumbing Maintenance Specialists

Font styles to use
Sans Serif

Requirements
Must have
• Logo
• Business name, contact number, email address, web address
• Domestic | Commercial | Industrial Est Since 1988
Nice to have
• Possibly a black card with a flame logo to one side
Should not have
• Spelling errors

```html
<!DOCTYPE html>
<html lang="en">
<head>
<meta charset="utf-8">
<title>Brintel Works – Business Card</title>
<link rel="stylesheet" href="https://fonts.googleapis.com/css2?family=Open+Sans:wght@400&display=swap">
<style>
  :root {
    --page: #e9e6e1;
    --card: #0b0b0b;
    --white: #ffffff;
    --yellow: #f4d20a;
    --orange: #f07b22;
    --red: #ec2329;
  }
  * { margin: 0; padding: 0; box-sizing: border-box; }
  html, body { width: 1200px; height: 900px; overflow: hidden; }
  body {
    background: var(--page);
    font-family: "Open Sans", Arial, sans-serif;
    position: relative;
  }
  .card {
    position: absolute;
    width: 600px;
    height: 343px;
    background: var(--card);
    overflow: hidden;
    box-shadow: 0 6px 18px rgba(0,0,0,.25);
  }
  .card--front { left: 300px; top: 50px; }
  .card--back  { left: 300px; top: 507px; }

  .brand {
    position: absolute;
    display: flex;
    align-items: center;
    gap: 16px;
    font-weight: 400;
    line-height: 1;
  }
  .brand__dot { border-radius: 50%; flex: none; }
  .brand__name { display: flex; flex-direction: column; }
  .brand__main { font-size: 46px; letter-spacing: 1px; }
  .brand__sub { font-size: 15px; letter-spacing: 4px; margin-top: 6px; }

  .card--front .brand { left: 110px; top: 118px; color: var(--white); }
  .card--front .brand__dot { width: 56px; height: 56px; background: var(--white); }

  .card--back .brand { left: 300px; top: 118px; color: var(--yellow); }
  .card--back .brand__dot { width: 40px; height: 40px; background: var(--red); }
  .card--back .brand__main { font-size: 34px; }
  .card--back .brand__sub { font-size: 11px; letter-spacing: 3px; }

  .contact {
    position: absolute;
    left: 26px;
    top: 24px;
    list-style: none;
    color: var(--yellow);
    font-size: 13px;
    line-height: 18px;
  }
  .contact li { display: flex; align-items: center; gap: 9px; }
  .contact svg { width: 10px; height: 10px; fill: var(--orange); flex: none; }

  .address {
    position: absolute;
    left: 26px;
    top: 150px;
    color: var(--yellow);
    font-size: 13px;
    line-height: 18px;
    font-style: normal;
  }
  .sectors {
    position: absolute;
    left: 26px;
    top: 200px;
    color: var(--yellow);
    font-size: 14px;
  }
  .bands { position: absolute; left: 0; bottom: 0; width: 600px; height: 110px; }
</style>
</head>
<body>

  <section class="card card--front" aria-label="Card front">
    <div class="brand">
      <span class="brand__dot"></span>
      <span class="brand__name">
        <span class="brand__main">Brintel Works</span>
        <span class="brand__sub">PTY LTD</span>
      </span>
    </div>
  </section>

  <section class="card card--back" aria-label="Card back">
    <ul class="contact">
      <li>
        <svg viewBox="0 0 10 10"><path d="M2 0.5 L4 2.8 L3 4 Q4.3 6 6 7 L7.2 6 L9.5 8 L8 9.6 Q3.5 9 0.4 2 Z"/></svg>
        07 3918 4726
      </li>
      <li>
        <svg viewBox="0 0 10 10"><path d="M0 2 H10 V8.5 H0 Z M0.8 2.6 L5 5.6 L9.2 2.6" stroke="#0b0b0b" stroke-width="0.8"/></svg>
        admin@brintelworks.com.au
      </li>
      <li>
        <svg viewBox="0 0 10 10"><circle cx="5" cy="5" r="4.6"/><path d="M0.6 5 H9.4 M5 0.4 V9.6" stroke="#0b0b0b" stroke-width="0.8"/></svg>
        www.brintelworks.com.au
      </li>
    </ul>

    <address class="address">
      12345, Address Goes Here<br>
      Country Name, 123456.
    </address>

    <p class="sectors">Domestic | Commercial | Industrial Est Since 1988</p>

    <div class="brand">
      <span class="brand__dot"></span>
      <span class="brand__name">
        <span class="brand__main">Brintel Works</span>
        <span class="brand__sub">PTY LTD</span>
      </span>
    </div>

    <svg class="bands" viewBox="0 0 600 110" aria-hidden="true">
      <polygon points="0,18 278,18 266,40 0,40" fill="var(--orange)"/>
      <polygon points="288,18 600,18 600,110 246,110 260,84 0,84 0,84 276,40" fill="var(--red)"/>
      <polygon points="0,40 266,40 252,84 0,84" fill="var(--card)"/>
    </svg>
  </section>

</body>
</html>
```